PTA Meeting Poster

We are looking to create a poster to invite parents of our school to our monthly PTA Meeting.

The copy should include:

PTA Meeting
This Wednesday
8:40am
in the Multi Purpose Room

All Welcome!

```html
<!DOCTYPE html>
<html lang="en">
<head>
<meta charset="utf-8">
<title>PTA Meeting Poster</title>
<link rel="stylesheet" href="https://fonts.googleapis.com/css2?family=Anton&family=Lato:wght@400;700&display=swap">
<style>
  :root {
    --page-bg: #e9e9e9;
    --board-dark: #080808;
    --board-mid: #2a2a2a;
    --board-glow: #6a6a6a;
    --chalk: #ffffff;
    --chalk-soft: #d9d9d9;
    --chalk-outline: #3a3a3a;
    --desk-light: #bdbdbd;
    --desk-dark: #7a7a7a;
  }
  * { margin: 0; padding: 0; box-sizing: border-box; }
  html, body {
    width: 1200px;
    height: 909px;
    overflow: hidden;
    background: var(--page-bg);
  }
  .canvas {
    position: relative;
    width: 1200px;
    height: 909px;
  }
  .poster {
    position: absolute;
    left: 268px;
    top: 0;
    width: 663px;
    height: 909px;
    overflow: hidden;
    background:
      radial-gradient(ellipse 70% 22% at 50% 0%, var(--board-glow) 0%, var(--board-mid) 45%, transparent 100%),
      linear-gradient(180deg, var(--board-mid) 0%, var(--board-dark) 30%, var(--board-dark) 100%);
    font-family: 'Lato', sans-serif;
    color: var(--chalk);
    text-align: center;
  }
  .poster__title {
    position: absolute;
    top: 112px;
    left: 0;
    width: 100%;
    font-family: 'Anton', sans-serif;
    font-size: 108px;
    line-height: 1;
    letter-spacing: -1px;
    color: var(--chalk);
    -webkit-text-stroke: 3px var(--chalk-outline);
    text-shadow: 0 3px 0 var(--chalk-soft);
  }
  .rule {
    position: absolute;
    height: 3px;
    background: var(--chalk);
  }
  .rule--top { top: 285px; left: 124px; width: 405px; }
  .rule--bottom { top: 578px; left: 193px; width: 264px; }
  .details {
    position: absolute;
    top: 318px;
    left: 0;
    width: 663px;
    line-height: 1;
    text-transform: uppercase;
  }
  .details__day { font-size: 41px; font-weight: 400; }
  .details__time { font-size: 76px; font-weight: 700; margin-top: 2px; }
  .details__place { font-size: 33px; font-weight: 400; margin-top: 8px; line-height: 1.36; }
  .welcome {
    position: absolute;
    top: 600px;
    left: 240px;
    width: 400px;
    font-size: 62px;
    line-height: 1.35;
    font-weight: 400;
    color: var(--chalk-soft);
    text-transform: uppercase;
    -webkit-text-stroke: 1px var(--chalk-outline);
  }
  .welcome__line { display: block; }
  .welcome__line--first { padding-right: 30px; }
  .desk {
    position: absolute;
    left: 0;
    bottom: 0;
    width: 663px;
    height: 55px;
    background: linear-gradient(180deg, var(--desk-light) 0%, var(--desk-dark) 100%);
  }
  .still-life {
    position: absolute;
    left: 0;
    top: 640px;
    width: 296px;
    height: 269px;
    background: radial-gradient(ellipse 70% 60% at 45% 55%, #8a8a8a 0%, #4a4a4a 55%, transparent 100%);
  }
</style>
</head>
<body>
  <main class="canvas">
    <article class="poster">
      <h1 class="poster__title">PTA MEETING</h1>
      <div class="rule rule--top"></div>
      <section class="details">
        <p class="details__day">This Wednesday</p>
        <p class="details__time">8:40AM</p>
        <p class="details__place">In the<br>Multi Purpose<br>Room</p>
      </section>
      <div class="rule rule--bottom"></div>
      <p class="welcome">
        <span class="welcome__line welcome__line--first">All</span>
        <span class="welcome__line">Welcome!</span>
      </p>
      <div class="desk"></div>
      <div class="still-life" role="img" aria-label="An apple resting on a stack of books with a piece of chalk on a desk"></div>
    </article>
  </main>
</body>
</html>
```